Design a web site for my business - Brightline Coatings Co.

We are a family business that handles design, fabrication and installation of powder coated aluminum, stainless steel and glass products. Including handrails, privacy slat screens, electric gates and pool fencing. We are based in the Whitsundays in North Queensland and service an area from Airlie Beach to Townsville.

Target Market(s)

Domestic and commercial

Industry/Entity Type

fabrication - manufacturing

Coding

Coded - Design and coding required

Number of Pages Required

5+ page

Colors
0054AA
0677BA
7BADD7
CADEEF
E8F1F8

Requirements
Must have
• photo galleries, contact page, one page for privacy screens, balustrades, glass fencing, stainless steel handrail, powder coated aluminium handrails and pool fencing

```html
<!DOCTYPE html>
<html lang="en">
<head>
<meta charset="utf-8">
<title>Brightline Coatings Co – Homepage Option 1</title>
<link href="https://fonts.googleapis.com/css2?family=Inter:wght@400;500;600&display=swap" rel="stylesheet">
<style>
:root{
  --blue:#0054AA;
  --blue-mid:#0677BA;
  --blue-soft:#7BADD7;
  --sky:#CADEEF;
  --mist:#E8F1F8;
  --ink:#0f1b2d;
  --body:#3a4656;
  --white:#ffffff;
  --line:#d7dee7;
}
*{box-sizing:border-box;margin:0;padding:0}
html,body{width:1200px;height:1200px;overflow:hidden}
body{background:var(--sky);font-family:"Inter",sans-serif;color:var(--ink);position:relative}
.board-title{position:absolute;left:0;width:700px;top:16px;text-align:center;font-size:22px;font-weight:600;letter-spacing:-.3px}
.page{position:absolute;background:var(--white);overflow:hidden}
.page--left{left:100px;top:67px;width:499px;height:1133px}
.page--right{left:637px;top:0;width:500px;height:1186px}
.abs{position:absolute}
.photo{position:absolute;border-radius:7px}
.eyebrow{position:absolute;font-size:6.4px;font-weight:600;letter-spacing:.6px;color:var(--blue);text-transform:uppercase}
.h2{position:absolute;font-size:15.5px;line-height:16.3px;font-weight:500;letter-spacing:-.3px;color:var(--ink)}
.p{position:absolute;font-size:6px;line-height:9.3px;color:var(--body)}
.link{position:absolute;font-size:5.6px;font-weight:500;color:var(--blue);padding-bottom:3px;border-bottom:.7px solid var(--blue);display:flex;align-items:center;gap:3px}
.btn{position:absolute;height:16px;border-radius:9px;font-size:5.6px;font-weight:500;display:flex;align-items:center;justify-content:center}
/* nav */
.nav{position:absolute;left:47px;top:8px;width:406px;height:26px;background:var(--white);border-radius:14px;display:flex;align-items:center}
.brand{position:absolute;left:14px;display:flex;align-items:center;gap:3px;font-size:5px;font-weight:600;color:var(--ink)}
.brand__dot{width:8px;height:8px;border-radius:50%;background:var(--blue)}
.nav__links{position:absolute;left:114px;display:flex;gap:14px;font-size:5.6px;color:var(--ink)}
.nav .btn{left:335px;width:65px;background:var(--blue);color:var(--white)}
/* hero */
.hero{position:absolute;left:0;top:0;width:499px;height:284px;background:linear-gradient(180deg,#0f58b8 0%,#3a7fcc 38%,#7bb0df 60%,#eef3f6 72%,#e6edf0 88%,#8cc25a 96%,#79b24a 100%)}
.hero__title{position:absolute;left:0;width:499px;top:70px;text-align:center;font-size:21px;line-height:19.5px;color:var(--white);letter-spacing:-.3px}
.hero__sub{position:absolute;left:0;width:499px;top:116px;text-align:center;font-size:6px;line-height:8.2px;color:var(--white)}
.hero .btn--dark{left:186px;top:140px;width:64px;background:#0a3f86;color:var(--white)}
.hero .btn--ghost{left:256px;top:140px;width:57px;background:rgba(255,255,255,.3);color:var(--white)}
/* why */
.why{position:absolute;left:0;top:542px;width:499px;height:284px;background:linear-gradient(180deg,var(--mist) 0%,var(--mist) 65%,#fff 100%)}
.feature{position:absolute;top:93px;width:94px;height:89px;background:var(--white);border-radius:5px}
.feature__icon{position:absolute;left:7px;top:11px;width:20px;height:20px;border-radius:4px;background:var(--mist);display:flex;align-items:center;justify-content:center}
.feature__title{position:absolute;left:7px;top:42px;font-size:6.2px;font-weight:500}
.feature__text{position:absolute;left:7px;top:55px;width:82px;font-size:5.2px;line-height:7.6px;color:var(--body)}
.svc-title{position:absolute;font-size:10px;font-weight:500;letter-spacing:-.2px}
/* stats */
.stats{position:absolute;left:46px;top:205px;width:406px;height:130px;border-radius:8px;background:linear-gradient(135deg,#0a5bbd,var(--blue) 60%,#0b66b8)}
.stats__title{position:absolute;left:0;width:406px;top:23px;text-align:center;color:var(--white);font-size:15px;line-height:16px;font-weight:500}
.stat{position:absolute;top:78px;color:var(--white)}
.stat__num{font-size:15px;font-weight:500}
.stat__label{font-size:6px;margin-top:3px;opacity:.9}
.stats__rule{position:absolute;top:73px;width:.7px;height:34px;background:rgba(255,255,255,.35)}
/* list */
.svc-list{position:absolute;left:46px;width:178px}
.svc-row{position:absolute;left:0;width:178px;font-size:6px;font-weight:500}
.svc-row svg{position:absolute;right:2px;top:0}
.rule{position:absolute;left:0;width:178px;height:.7px;background:var(--line)}
/* testimonials */
.reviews{position:absolute;left:0;top:602px;width:500px;height:264px;background:linear-gradient(180deg,var(--mist) 0%,var(--mist) 60%,#fff 100%)}
.review{position:absolute;top:81px;width:129px;height:148px;background:var(--white);border-radius:5px}
.review__mark{position:absolute;left:10px;top:17px;font-size:20px;line-height:10px;font-weight:600;color:var(--blue-soft)}
.review__text{position:absolute;left:10px;top:40px;width:112px;font-size:6px;line-height:10.7px;color:var(--ink)}
.review__avatar{position:absolute;left:10px;top:120px;width:20px;height:20px;border-radius:50%;background:linear-gradient(135deg,#b9a48c,#6e5d4d)}
.review__name{position:absolute;left:37px;top:122px;font-size:6px;font-weight:600}
.review__role{position:absolute;left:37px;top:131px;font-size:5px;color:var(--body)}
/* cta */
.cta{position:absolute;left:0;top:866px;width:500px;height:155px;background:linear-gradient(90deg,#2d5685 0%,#3f6b99 45%,#5a80a8 75%,#8fa8bf 100%)}
.cta .h2{color:var(--white)}
.cta .btn--light{left:46px;top:103px;width:65px;background:var(--white);color:var(--ink)}
.cta .btn--ghost{left:117px;top:103px;width:38px;background:rgba(255,255,255,.25);color:var(--white)}
/* footer */
.footer{position:absolute;left:0;top:1021px;width:500px;height:140px;background:var(--mist)}
.footer__head{position:absolute;top:20px;font-size:6.2px;font-weight:500}
.footer__list{position:absolute;top:38px;list-style:none;font-size:4.7px;line-height:12.4px;color:var(--body)}
.social{position:absolute;top:102px;width:6px;height:6px;border-radius:50%;background:#5b6675}
.contact{position:absolute;left:352px;display:flex;gap:5px;font-size:4.7px;line-height:6.5px;color:var(--ink)}
.bottom-bar{position:absolute;left:0;top:1161px;width:500px;height:25px;background:var(--white);font-size:4.8px;color:var(--body)}
</style>
</head>
<body>

<div class="board-title">Option-1</div>

<!-- LEFT COLUMN -->
<main class="page page--left">
  <section class="hero" role="img" aria-label="White picket fence on green grass under a bright blue sky with clouds">
    <nav class="nav">
      <div class="brand"><span class="brand__dot"></span>Brightline Coatings Co</div>
      <div class="nav__links"><span>About</span><span>Services</span><span>Projects</span><span>Testimonials</span><span>Contacts</span></div>
      <span class="btn">Get a Free Quote</span>
    </nav>
    <h1 class="hero__title">Custom Fabrication<br>for Modern Living</h1>
    <p class="hero__sub">Precision-crafted aluminium, stainless steel, and glass solutions for<br>homes and businesses across North Queensland.</p>
    <span class="btn btn--dark">Get a Free Quote</span>
    <span class="btn btn--ghost">View Projects</span>
  </section>

  <section class="about">
    <div class="eyebrow" style="left:47px;top:339px">Crafting quality that lasts</div>
    <h2 class="h2" style="left:47px;top:352px">Built by Locals for the<br>Unique Whitsunday<br>Environment</h2>
    <p class="p" style="left:47px;top:410px;width:162px">At Brightline Coatings Co, we don't just build enclosures; we engineer structural statements that thrive in harsh coastal conditions. Our family-owned operation bridges the gap between industrial durability and architectural elegance.</p>
    <span class="link" style="left:47px;top:477px">Learn more about us
      <svg width="7" height="5" viewBox="0 0 7 5"><path d="M0 2.5h6M4 .5l2 2-2 2" fill="none" stroke="#0054AA" stroke-width=".7"/></svg></span>
    <div class="photo" role="img" aria-label="Timber-capped black balustrade along a coastal boardwalk" style="left:255px;top:317px;width:198px;height:125px;background:linear-gradient(160deg,#4f6a86,#6b5a45 50%,#8a8f92)"></div>
    <div class="photo" role="img" aria-label="White slatted aluminium gate under blue sky" style="left:255px;top:445px;width:97px;height:63px;background:linear-gradient(180deg,#2f6fc4,#dfe3e6 60%,#9aa3a8)"></div>
    <div class="photo" role="img" aria-label="Timber deck walkway with stainless handrail among gardens" style="left:356px;top:445px;width:97px;height:63px;background:linear-gradient(160deg,#5f7d4a,#8a5a3c 60%,#6f7f5a)"></div>
  </section>

  <section class="why">
    <div class="eyebrow" style="left:0;width:499px;text-align:center;top:29px">Why choose us</div>
    <h2 class="h2" style="left:0;width:499px;text-align:center;top:44px">The Fence Company<br>You Can Rely On</h2>

    <div class="feature" style="left:47px">
      <div class="feature__icon"><svg width="10" height="10" viewBox="0 0 10 10" fill="none" stroke="#0054AA" stroke-width=".8"><rect x="2" y="1.5" width="6" height="3" rx=".5"/><path d="M5 4.5v1.5M4.3 6h1.4v3H4.3z"/></svg></div>
      <div class="feature__title">Custom Designed</div>
      <div class="feature__text">Every solution is tailored to match your project and requirements.</div>
    </div>
    <div class="feature" style="left:151px">
      <div class="feature__icon"><svg width="10" height="10" viewBox="0 0 10 10" fill="none" stroke="#0054AA" stroke-width=".8"><circle cx="5" cy="2.3" r="1"/><path d="M5 3.3L2.5 9M5 3.3L7.5 9M3.4 6.5h3.2"/></svg></div>
      <div class="feature__title">Premium Finishes</div>
      <div class="feature__text">Durable powder-coated and stainless steel finishes built to last.</div>
    </div>
    <div class="feature" style="left:255px">
      <div class="feature__icon"><svg width="10" height="10" viewBox="0 0 10 10" fill="none" stroke="#0054AA" stroke-width=".8"><circle cx="3.3" cy="3.5" r="1.2"/><circle cx="6.7" cy="3.5" r="1.2"/><path d="M1 8a2.3 2.3 0 014.6 0M4.4 8A2.3 2.3 0 019 8"/></svg></div>
      <div class="feature__title">Experienced Team</div>
      <div class="feature__text">Skilled professionals delivering quality craftsmanship from start to finish.</div>
    </div>
    <div class="feature" style="left:359px">
      <div class="feature__icon"><svg width="10" height="10" viewBox="0 0 10 10" fill="none" stroke="#0054AA" stroke-width=".8"><rect x="1.5" y="3" width="7" height="5" rx=".6"/><path d="M3.8 3V2h2.4v1M1.5 5.3h7"/></svg></div>
      <div class="feature__title">Australian Standards</div>
      <div class="feature__text">Designed and installed to meet Australian safety and quality standards.</div>
    </div>
  </section>

  <section class="services">
    <div class="eyebrow" style="left:47px;top:780px">Core capabilities</div>
    <h2 class="h2" style="left:47px;top:795px">Specialized<br>Fabrication Services</h2>
    <p class="p" style="left:324px;top:792px;width:130px">Providing high-performance architectural metalwork for luxury homes and large-scale commercial developments.</p>

    <div class="photo" role="img" aria-label="Black laser-cut decorative privacy screen panels" style="left:47px;top:851px;width:198px;height:125px;background:linear-gradient(135deg,#1b1b1b,#3d4a36 50%,#202020)"></div>
    <div class="svc-title" style="left:47px;top:985px">Privacy Screens</div>
    <p class="p" style="left:47px;top:999px;width:190px">Custom-slatted or decorative laser-cut solutions providing secluded spaces without compromising tropical airflow.</p>
    <span class="link" style="left:47px;top:1026px">Learn more <svg width="7" height="5" viewBox="0 0 7 5"><path d="M0 2.5h6M4 .5l2 2-2 2" fill="none" stroke="#0054AA" stroke-width=".7"/></svg></span>

    <div class="photo" role="img" aria-label="Red aluminium balustrade on a tiled balcony overlooking the bay" style="left:255px;top:851px;width:198px;height:125px;background:linear-gradient(180deg,#8fb0cf,#9b6a5a 45%,#b7aa96)"></div>
    <div class="svc-title" style="left:255px;top:985px">Balustrades</div>
    <p class="p" style="left:255px;top:999px;width:190px">Architectural stainless steel, glass, or aluminium balustrades engineered for uncompromising safety and flow.</p>
    <span class="link" style="left:255px;top:1026px">Learn more <svg width="7" height="5" viewBox="0 0 7 5"><path d="M0 2.5h6M4 .5l2 2-2 2" fill="none" stroke="#0054AA" stroke-width=".7"/></svg></span>

    <div class="photo" role="img" aria-label="Frameless glass pool fence among tropical plants" style="left:47px;top:1069px;width:198px;height:100px;background:linear-gradient(160deg,#3d5a3a,#8fa89a 60%,#c9d6d2)"></div>
    <div class="photo" role="img" aria-label="Timber-look slatted gate between brick pillars" style="left:255px;top:1069px;width:198px;height:100px;background:linear-gradient(160deg,#7d8f6a,#a8653a 55%,#3a3a3a)"></div>
  </section>
</main>

<!-- RIGHT COLUMN -->
<main class="page page--right">
  <section class="services-cont">
    <div class="photo" role="img" aria-label="Powder coated balustrade along a coastal boardwalk" style="left:46px;top:-8px;width:198px;height:115px;background:linear-gradient(160deg,#4f6a86,#8a5a35 55%,#8a8f92)"></div>
    <div class="svc-title" style="left:46px;top:117px">Powder Coating</div>
    <p class="p" style="left:46px;top:131px;width:190px">Industrial-grade finishes in over 200+ colors, cured in-house for maximum resistance to UV and salt spray.</p>
    <span class="link" style="left:46px;top:158px">Learn more <svg width="7" height="5" viewBox="0 0 7 5"><path d="M0 2.5h6M4 .5l2 2-2 2" fill="none" stroke="#0054AA" stroke-width=".7"/></svg></span>

    <div class="photo" role="img" aria-label="Dark framed glass fabrication on a building terrace" style="left:255px;top:-8px;width:197px;height:115px;background:linear-gradient(160deg,#3b4248,#7a8288 55%,#2e3338)"></div>
    <div class="svc-title" style="left:255px;top:117px">Custom Fabrication</div>
    <p class="p" style="left:255px;top:131px;width:190px">Bespoke structural metalwork designed to fulfill unique architectural visions and complex site requirements.</p>
    <span class="link" style="left:255px;top:158px">Learn more <svg width="7" height="5" viewBox="0 0 7 5"><path d="M0 2.5h6M4 .5l2 2-2 2" fill="none" stroke="#0054AA" stroke-width=".7"/></svg></span>
  </section>

  <section class="stats">
    <h2 class="stats__title">Delivering Quality Without<br>Compromise</h2>
    <div class="stat" style="left:37px"><div class="stat__num">500+</div><div class="stat__label">Project Completed</div></div>
    <span class="stats__rule" style="left:115px"></span>
    <div class="stat" style="left:133px"><div class="stat__num">15+</div><div class="stat__label">Years Experience</div></div>
    <span class="stats__rule" style="left:204px"></span>
    <div class="stat" style="left:229px"><div class="stat__num">100%</div><div class="stat__label">Customer Satisfaction</div></div>
    <span class="stats__rule" style="left:309px"></span>
    <div class="stat" style="left:325px"><div class="stat__num">6+</div><div class="stat__label">Core Services</div></div>
  </section>

  <section class="install">
    <div class="eyebrow" style="left:46px;top:370px">Custom solution</div>
    <h2 class="h2" style="left:46px;top:384px">Expert Installation &amp;<br>Repair Service</h2>
    <p class="p" style="left:46px;top:423px;width:160px">We provide professional fence installation, repair, and custom solutions to match your style and needs.</p>
    <div class="svc-list" style="top:458px">
      <div class="svc-row" style="top:0">New Fence Installtion<svg width="6" height="6" viewBox="0 0 6 6"><path d="M1 5l4-4M2 1h3v3" fill="none" stroke="#0f1b2d" stroke-width=".6"/></svg></div>
      <span class="rule" style="top:14px"></span>
      <div class="svc-row" style="top:23px;font-size:9.5px">Fence Repair &amp; Installation<svg width="7" height="6" viewBox="0 0 7 6"><path d="M0 3h6M4 1l2 2-2 2" fill="none" stroke="#0054AA" stroke-width=".6"/></svg></div>
      <p class="p" style="left:0;top:38px;width:150px">We fix damaged posts, panels, and gate or replace old fence entirely, to restore security and style.</p>
      <span class="rule" style="top:62px"></span>
      <div class="svc-row" style="top:71px">Custom Gate Installation<svg width="6" height="6" viewBox="0 0 6 6"><path d="M1 5l4-4M2 1h3v3" fill="none" stroke="#0f1b2d" stroke-width=".6"/></svg></div>
      <span class="rule" style="top:85px"></span>
      <div class="svc-row" style="top:94px">Fence Maintenance<svg width="6" height="6" viewBox="0 0 6 6"><path d="M1 5l4-4M2 1h3v3" fill="none" stroke="#0f1b2d" stroke-width=".6"/></svg></div>
    </div>
    <div class="photo" role="img" aria-label="Courtyard with timber fence, pergola and wicker outdoor furniture" style="left:255px;top:364px;width:197px;height:202px;background:linear-gradient(170deg,#d9dbd8,#b89b72 45%,#7c6a55 70%,#c7c2b8)"></div>
  </section>

  <section class="reviews">
    <div class="eyebrow" style="left:0;width:500px;text-align:center;top:28px">Testiminials</div>
    <h2 class="h2" style="left:0;width:500px;text-align:center;top:43px">What Our Client Says</h2>

    <article class="review" style="left:46px">
      <div class="review__mark">“</div>
      <p class="review__text">The precision Brightline achieved on our frameless glass balustrades was breathtaking. Their expertise in coastal finishes gave us complete peace of mind for our beachfront build."</p>
      <div class="review__avatar" role="img" aria-label="Client portrait"></div>
      <div class="review__name">Marcus Hale</div>
      <div class="review__role">Airlie Beach Developer</div>
    </article>
    <article class="review" style="left:185px">
      <div class="review__mark">“</div>
      <p class="review__text">Unmatched reliability. As a commercial developer, I appreciate their adherence to strict timelines and the superior quality of their automatic gate installations."</p>
      <div class="review__avatar" role="img" aria-label="Client portrait"></div>
      <div class="review__name">Leah Corwin</div>
      <div class="review__role">Director, LC Construction</div>
    </article>
    <article class="review" style="left:324px">
      <div class="review__mark">“</div>
      <p class="review__text">They transformed our home with custom-designed privacy screens. The powder coat finish is flawless and the installation was incredibly professional."</p>
      <div class="review__avatar" role="img" aria-label="Client portrait"></div>
      <div class="review__name">The Ashfords</div>
      <div class="review__role">Hamilton Island Residents</div>
    </article>
  </section>

  <section class="cta" role="img" aria-label="Grey slatted driveway gate with blue tint overlay">
    <h2 class="h2" style="left:46px;top:35px">Ready to Start Your<br>Next Project?</h2>
    <p class="p" style="left:46px;top:74px;width:160px;color:#e8f1f8">Supporting text encouraging users to request a free consultation and quote.</p>
    <span class="btn btn--light">Get a Free Quote</span>
    <span class="btn btn--ghost">Call Us</span>
  </section>

  <footer class="footer">
    <div class="brand" style="left:46px;top:22px"><span class="brand__dot"></span>Brightline Coatings Co</div>
    <p class="p" style="left:46px;top:57px;width:92px;font-size:4.7px;line-height:7.6px">Family-owned specialists delivering custom structural solutions across the Whitsundays. Precision engineered for tropical durability, designed for timeless beauty.</p>
    <span class="social" style="left:49px"></span>
    <span class="social" style="left:63px"></span>
    <span class="social" style="left:77px"></span>

    <div class="footer__head" style="left:170px">Quick Links</div>
    <ul class="footer__list" style="left:170px"><li>About</li><li>Services</li><li>Project</li><li>Testimonials</li><li>Contact us</li></ul>

    <div class="footer__head" style="left:259px">Services</div>
    <ul class="footer__list" style="left:259px"><li>Privacy Screens</li><li>Balustrades</li><li>Glass Pool Fencing</li><li>Automatic Gates</li><li>Powder Coating</li></ul>

    <div class="footer__head" style="left:352px">Reach us</div>
    <div class="contact" style="top:40px">
      <svg width="7" height="6" viewBox="0 0 7 6"><rect x=".3" y=".5" width="6.4" height="5" rx="1" fill="#0054AA"/><path d="M1 1.5l2.5 2 2.5-2" fill="none" stroke="#fff" stroke-width=".6"/></svg>
      <span>27 Harbour Works Lane,<br>Cannonvale QLD 4802</span></div>
    <div class="contact" style="top:66px">
      <svg width="7" height="7" viewBox="0 0 7 7"><rect x="1.5" y=".3" width="4" height="6.4" rx=".9" fill="none" stroke="#0054AA" stroke-width=".7"/></svg>
      <span>(07) 5550 1842</span></div>
    <div class="contact" style="top:82px">
      <svg width="7" height="7" viewBox="0 0 7 7"><path d="M3.5.3A2.5 2.5 0 001 2.8C1 4.6 3.5 6.8 3.5 6.8S6 4.6 6 2.8A2.5 2.5 0 003.5.3z" fill="#0054AA"/><circle cx="3.5" cy="2.8" r=".9" fill="#fff"/></svg>
      <span>hello@brightlinecoatings.com.au</span></div>
  </footer>

  <div class="bottom-bar">
    <span class="abs" style="left:46px;top:10px">© 2024 Brightline Coatings Co. All Rights Reserved.</span>
    <span class="abs" style="left:334px;top:10px">Privacy Policy</span>
    <span class="abs" style="left:380px;top:10px">Terms of Service</span>
    <span class="abs" style="left:433px;top:10px">Sitemap</span>
  </div>
</main>

</body>
</html>
```